New Business Cards for Tormin Group

We need a new Business Card to compliment our new logo. We are a vibrant design, manufacture and install business providing recreation areas, public parks and Municipal spaces. We want business cards that are classy, modern and clean.

We have recently changed our logo, and are celebrating our 40th anniversary. We want business cards with a new modern design to reflect our status.

Target Market(s)

Customers

Contact Information for Business Card

We need all the details of our 3 offices as per the business card attached. Please disregard the old logo on the business card, the other three files show our new logo.

Requirements
Must have
• All info as per attached business card but with new logo.
Nice to have

```html
<!DOCTYPE html>
<html lang="en">
<head>
<meta charset="utf-8">
<title>Tormin Group – Business Card</title>
<link href="https://fonts.googleapis.com/css2?family=Lato:wght@400;700&display=swap" rel="stylesheet">
<style>
  :root {
    --brand-red: #e8323c;
    --ink-dark: #333336;
    --ink-body: #5a5a5e;
    --rule-light: #d9d9d9;
    --swoosh-dark: #3a3a3d;
    --card-white: #ffffff;
    --backdrop: #2a2a2a;
  }
  * { margin: 0; padding: 0; box-sizing: border-box; }
  html, body {
    width: 1200px;
    height: 1200px;
    overflow: hidden;
    background: var(--backdrop);
    font-family: "Lato", Arial, sans-serif;
  }
  .business-card {
    position: absolute;
    left: 100px;
    top: 307px;
    width: 1000px;
    height: 585px;
    background: var(--card-white);
    border-radius: 34px;
    overflow: hidden;
  }
  .name-tab {
    position: absolute;
    left: 0;
    top: 85px;
    width: 11px;
    height: 66px;
    background: var(--brand-red);
    border-radius: 0 6px 6px 0;
  }
  .person-name {
    position: absolute;
    left: 32px;
    top: 78px;
    font-size: 35px;
    font-weight: 700;
    color: var(--brand-red);
    letter-spacing: 0.2px;
  }
  .person-title {
    position: absolute;
    left: 32px;
    top: 124px;
    font-size: 23px;
    color: var(--ink-dark);
  }
  .brand-mark {
    position: absolute;
    right: 48px;
    top: 98px;
    display: flex;
    align-items: center;
    gap: 14px;
  }
  .brand-dot {
    width: 46px;
    height: 46px;
    border-radius: 50%;
    background: var(--brand-red);
  }
  .brand-name {
    font-size: 38px;
    font-weight: 700;
    color: var(--ink-dark);
    letter-spacing: 0.5px;
  }
  .direct-contacts {
    position: absolute;
    left: 32px;
    top: 218px;
    list-style: none;
    font-size: 18px;
    line-height: 35px;
    color: var(--ink-dark);
  }
  .contact-label { color: var(--brand-red); }
  .section-rule {
    position: absolute;
    left: 32px;
    top: 335px;
    width: 920px;
    height: 2px;
    background: var(--rule-light);
  }
  .section-rule::before {
    content: "";
    position: absolute;
    left: 0;
    top: 0;
    width: 290px;
    height: 2px;
    background: var(--ink-body);
  }
  .office {
    position: absolute;
    top: 354px;
  }
  .office-head { left: 32px; }
  .office-dubai { left: 380px; }
  .office-doha { left: 700px; top: 357px; }
  .office-name {
    font-size: 24px;
    font-weight: 400;
    color: var(--brand-red);
    margin-bottom: 8px;
  }
  .office-lines {
    list-style: none;
    font-size: 18.5px;
    line-height: 29.5px;
    color: var(--ink-body);
  }
  .card-wave {
    position: absolute;
    left: 0;
    bottom: 0;
    width: 1000px;
    height: 75px;
  }
</style>
</head>
<body>
  <article class="business-card">
    <span class="name-tab"></span>
    <h1 class="person-name">Rami Nassour</h1>
    <p class="person-title">Managing Partner</p>

    <div class="brand-mark">
      <span class="brand-dot"></span>
      <span class="brand-name">TORMIN GROUP</span>
    </div>

    <ul class="direct-contacts">
      <li><span class="contact-label">Phone</span>: +971 (0)50 487 3920</li>
      <li><span class="contact-label">Email</span>: rami@tormingroup.com</li>
      <li><span class="contact-label">Web</span>: www.tormingroup.com</li>
    </ul>

    <div class="section-rule"></div>

    <section class="office office-head">
      <h2 class="office-name">Head Office</h2>
      <ul class="office-lines">
        <li>P.O. Box: 31842 Abu Dhabi. U.A.E</li>
        <li>Tel No: +971 (0)2 5372918</li>
        <li>Fax No: +971(0)2 5372917</li>
        <li>Email: sales@tormingroup.com</li>
      </ul>
    </section>

    <section class="office office-dubai">
      <h2 class="office-name">Dubai Office</h2>
      <ul class="office-lines">
        <li>P.O. Box: 417206 Dubai, U.A.E</li>
        <li>Tel No: +971 (0)4 382514</li>
        <li>Fax No: +971(0)4 382577</li>
        <li>Email: sales@tormingroup.com</li>
      </ul>
    </section>

    <section class="office office-doha">
      <h2 class="office-name">Qater Office</h2>
      <ul class="office-lines">
        <li>P.O. Box: 20873 Doha, Qatter</li>
        <li>Tel No: +974 44735018</li>
        <li>Fax No: +971 44619382</li>
        <li>Email: sales@tormingroup.com</li>
      </ul>
    </section>

    <svg class="card-wave" viewBox="0 0 1000 75" preserveAspectRatio="none" aria-hidden="true">
      <path d="M0,32 C120,38 240,44 300,46 C220,44 100,40 0,40 Z" fill="var(--swoosh-dark)"/>
      <path d="M560,30 C720,22 880,16 1000,14 L1000,22 C880,23 740,27 620,31 Z" fill="var(--swoosh-dark)"/>
      <path d="M0,46 C160,52 320,56 460,46 C620,35 800,25 1000,22 L1000,75 L0,75 Z" fill="var(--brand-red)"/>
    </svg>
  </article>
</body>
</html>
```